Drone service provider needs a brilliant web design

I need a responsive web design for a new drone service company. Pelham Drone Solutions provides turnkey solutions to capture, process, and deliver actionable aerial data to customers. The design should communicate a professional company that is safe, legal and insured. I included our logo design and business card designs for reference.
*content to be supplied after design selected

Target Market(s)

We serve telecommunications, construction, government, utility infrastructure, insurance and other industries.

Industry/Entity Type

Industrial

Number of Pages Required

5+ page

Colors

Designer to choose colors to be used in the design.

Requirements
Must have
• The design should highlight professional services to include Inspections, Mapping, Consulting and Training. The site should include aerial images and video to compliment the services offered. The landing page must include following sections in order: HOME, SERVICES, ABOUT, DEMO REEL, CLIENTS, CONTACT FORM, and social media buttons (Facebook, LinkedIn, Twitter, YouTube, Instagram). Contact: 615-382-9041 info@pelhamdronesolutions-example.com Smyrna, TN
• Sitemap:
• 6 pages: Home, Inspections, Mapping, Training, Consulting, About
• HOME (Landing Page)
• • Header with logo and tab links (Home, Services, About, Contact)
• • 'CAPTURE. PROCESS. DELIVER.' tagline and 'CONTACT US' button displayed within aerial image of drone over city or construction site
• • Services section with icons, text and read more link to page
• • About section with photo and text with three icons for SAFE. LEGAL. INSURED.
• • Demo reel
• • Clients logos shown scrolling horizontally
• • Contact form
• • Footer with logo, phone, email, social media buttons
• SERVICES (4 different pages)
• • Inspections
• • Mapping
• • Consulting
• • Training
• ABOUT page
• • Company
• • Partners
• • Certifications & Associations
• • Careers
• CONTACT linked to bottom of landing page
• Would you like to receive the newsletter? Yes or No Drop-down list
Nice to have
• Photos of KVR Marlin or Corvex inspecting infrastructure, buildings, construction sites, etc. A photo of one or two pilots in vest and helmet. Free stock photos preferred but would purchase the right photo that's more relevant.
• website references:
• https://www.quillrotor-example.com/
• https://www.brentfieldworks-example.com/services
• https://www.tomaro-example.com/
• http://gantrymetric-example.com/
• http://lumbrook-example.com/
• http://fennotics-example.com/
• https://www.grebe-example.io/
Should not have
• not an aerial photography or videography service business, no blog or newsletter

```html
<!DOCTYPE html>
<html lang="en">
<head>
<meta charset="utf-8">
<title>Pelham Drone Solutions</title>
<link href="https://fonts.googleapis.com/css2?family=Lato:ital,wght@0,400;0,700;0,900;1,400&display=swap" rel="stylesheet">
<style>
:root{
  --blue:#0f6fc0;
  --blue-dark:#0a5aa3;
  --ink:#1c1c1c;
  --text:#444;
  --light:#efefef;
  --footer:#262626;
  --white:#fff;
}
*{box-sizing:border-box;margin:0;padding:0}
html,body{width:1200px;height:3403px;overflow:hidden}
body{font-family:'Lato',sans-serif;color:var(--text);background:var(--white);position:relative}
.abs{position:absolute}
.topbar{top:0;left:0;width:1200px;height:46px;background:#f3f3f3}
.social{display:flex;gap:14px;align-items:center}
.social span{width:18px;height:18px;border-radius:50%;background:#777;display:block}
.topbar .social{position:absolute;left:75px;top:14px}
.call{position:absolute;right:75px;top:0;height:46px;width:350px;background:var(--blue);color:#fff;font-weight:700;font-size:19px;display:flex;align-items:center;justify-content:center;gap:10px;clip-path:polygon(8% 0,100% 0,92% 100%,0 100%)}
.nav{top:46px;left:0;width:1200px;height:99px;background:#fff}
.logo{position:absolute;left:75px;top:20px;line-height:1}
.logo b{display:block;font-size:44px;font-weight:900;color:var(--ink);letter-spacing:1px}
.logo small{display:block;font-size:13px;font-weight:700;color:var(--blue);letter-spacing:4.6px;margin-top:2px}
.menu{position:absolute;right:75px;top:42px;display:flex;gap:44px;font-size:14px;font-weight:700;color:var(--ink)}
.menu .on{color:var(--blue)}
.hero{top:145px;left:0;width:1200px;height:517px;background:linear-gradient(120deg,#4d6f3a 0%,#6f8f4c 40%,#5b7a3b 70%,#7a8c3a 100%)}
.hero .tagline{position:absolute;left:75px;top:150px;color:#fff;font-size:20px;font-weight:900;letter-spacing:3px}
.hero h1{position:absolute;left:75px;top:182px;color:#fff;font-size:42px;font-weight:900}
.hero p{position:absolute;left:75px;top:236px;width:680px;color:#fff;font-size:23px;font-weight:700;line-height:1.35}
.btn{display:inline-block;background:var(--ink);color:#fff;font-weight:700;font-size:16px;text-align:center;line-height:46px;height:46px}
.btn.blue{background:var(--blue)}
.hero .btn{position:absolute;top:318px;width:182px}
.dots{display:flex;gap:7px}
.dots i{width:11px;height:11px;border-radius:50%;background:#fff;display:block}
.dots i.on{background:var(--blue)}
.hero .dots{position:absolute;left:75px;top:455px}
.quick{top:197px;left:792px;width:333px;height:415px;background:rgba(240,240,240,.93);padding:18px 27px}
.quick h3{text-align:center;font-size:27px;font-weight:900;color:var(--ink);margin-bottom:12px}
.quick h3 em,.title em{font-style:normal;color:var(--blue)}
.field{background:#fff;border:1px solid #cfcfcf;height:40px;margin-bottom:10px;font-size:13px;padding:11px 14px;color:#333}
.field.msg{height:78px}
.quick .submit{background:var(--blue);color:#fff;font-weight:700;text-align:center;height:48px;line-height:48px;font-size:16px;margin-top:6px}
.title{position:absolute;left:0;width:1200px;text-align:center;font-size:34px;font-weight:900;color:var(--ink)}
.service{top:789px;width:243px;height:291px;background:linear-gradient(180deg,var(--blue) 0%,var(--blue-dark) 100%);color:#fff;text-align:center;padding:38px 20px 0}
.service svg{width:66px;height:66px}
.service h4{font-size:19px;font-weight:700;margin:28px 0 12px}
.service p{font-size:13px;line-height:1.75}
.about{top:1148px;left:0;width:1200px;height:435px;background:var(--light);overflow:hidden}
.about-photo{position:absolute;left:0;top:0;width:490px;height:435px;background:linear-gradient(135deg,#d7dde0 0%,#9fb98a 45%,#4f7a32 100%)}
.about h2{position:absolute;left:525px;top:72px;font-size:33px;font-weight:700;color:var(--ink);line-height:1.05}
.about h2 span{color:var(--blue)}
.about p{position:absolute;left:525px;top:160px;width:600px;font-size:14px;line-height:1.7}
.about .btn{position:absolute;left:525px;top:290px;width:180px}
.badges{position:absolute;left:745px;top:284px;display:flex;gap:34px}
.badge{display:flex;flex-direction:column;align-items:center;gap:6px;font-size:13px;font-weight:900;color:var(--ink);letter-spacing:1px}
.badge svg{width:34px;height:34px}
.project{background:linear-gradient(135deg,#70805c,#a7b08d)}
.play{position:absolute;left:50%;top:50%;width:64px;height:64px;margin:-32px 0 0 -32px;border-radius:50%;background:#fff;display:flex;align-items:center;justify-content:center}
.solutions{top:2139px;left:0;width:1200px;height:417px;background:var(--light);overflow:hidden}
.solutions .lead{position:absolute;left:170px;top:100px;width:860px;text-align:center;font-size:14px;line-height:1.8}
.sol{position:absolute;top:175px;width:330px;text-align:center}
.sol svg{width:74px;height:74px}
.sol h4{color:var(--blue);font-size:22px;font-weight:700;margin:14px 0 6px}
.sol p{font-size:14px;line-height:1.75}
.avatar{top:2650px;left:545px;width:110px;height:110px;border-radius:50%;background:linear-gradient(180deg,#d9d9d9,#9c9c9c)}
.quote{top:2775px;left:100px;width:1000px;text-align:center;font-style:italic;font-size:16px;line-height:1.6;color:#333}
.person{top:2860px;left:0;width:1200px;text-align:center}
.person b{color:var(--blue);font-size:14px;display:block}
.person i{font-size:13px;color:#555}
.clients{top:2918px;left:75px;width:1050px;display:flex;justify-content:space-between}
.client{width:190px;height:56px;border:1px solid #d6d6d6;background:#f7f7f7;display:flex;align-items:center;justify-content:center;gap:8px;font-size:16px;font-weight:700;color:#777}
.client i{width:14px;height:14px;background:#9a9a9a;border-radius:50%;display:block}
.footer{top:3050px;left:0;width:1200px;height:353px;background:var(--footer);color:#ddd}
.footer h5{font-size:17px;font-weight:700;color:#fff;margin-bottom:18px}
.col{position:absolute;top:45px;font-size:14px;line-height:1.5}
.col li{list-style:none;margin-bottom:8px}
.flogo b{display:block;font-size:46px;font-weight:900;color:#fff;line-height:1}
.flogo small{display:block;font-size:13px;font-weight:700;color:#fff;letter-spacing:4.7px}
.footer .social span{background:#888}
.contact-line{display:flex;gap:12px;align-items:flex-start;margin-bottom:8px}
.contact-line svg{flex:0 0 14px;margin-top:3px}
</style>
</head>
<body>

<div class="abs topbar">
  <div class="social" aria-label="Social links"><span></span><span></span><span></span><span></span><span></span></div>
  <div class="call">
    <svg width="18" height="18" viewBox="0 0 24 24" fill="#fff"><path d="M6.6 10.8a15 15 0 0 0 6.6 6.6l2.2-2.2c.3-.3.7-.4 1-.2 1.1.4 2.3.6 3.6.6.6 0 1 .4 1 1V20c0 .6-.4 1-1 1A17 17 0 0 1 3 4c0-.6.4-1 1-1h3.5c.6 0 1 .4 1 1 0 1.3.2 2.5.6 3.6.1.3 0 .7-.2 1z"/></svg>
    CALL US: 615-382-9041
  </div>
</div>

<header class="abs nav">
  <div class="logo"><b>PELHAM</b><small>DRONE SOLUTIONS</small></div>
  <nav class="menu"><span class="on">HOME</span><span>ABOUT US</span><span>SERVICES</span><span>PROJECTS</span><span>CONTACT US</span></nav>
</header>

<section class="abs hero" role="img" aria-label="Aerial photo of a drone flying over green farmland with a mapping overlay">
  <div class="tagline">CAPTURE. PROCESS. DELIVER.</div>
  <h1>PELHAM DRONE SOLUTIONS</h1>
  <p>We provide turnkey solutions to capture, process, and deliver actionable aerial data to customers..</p>
  <span class="btn" style="left:75px">READ MORE</span>
  <span class="btn blue" style="left:273px">CONTACT US</span>
  <div class="dots"><i class="on"></i><i></i><i></i><i></i></div>
</section>

<form class="abs quick">
  <h3>QUICK <em>CONTACT</em></h3>
  <div class="field">Enter Name</div>
  <div class="field">Enter Email Address</div>
  <div class="field">Phone No</div>
  <div class="field">Subject</div>
  <div class="field msg">Message</div>
  <div class="submit">SUBMIT</div>
</form>

<h2 class="title" style="top:712px">OUR SERVICE <em>OFFERS</em></h2>

<div class="abs service" style="left:75px">
  <svg viewBox="0 0 24 24" fill="none" stroke="#fff" stroke-width="2.6"><circle cx="10" cy="10" r="6.5"/><path d="M15 15l6 6" stroke-linecap="round"/></svg>
  <h4>INSPECTIONS</h4><p>Vestibulum vel metus sit amet turpis bibendum tincidunt vel sit amet quam habitant morbi tristique senectus..</p>
</div>
<div class="abs service" style="left:345px">
  <svg viewBox="0 0 24 24" fill="#fff"><path d="M12 2a7 7 0 0 0-7 7c0 5 7 13 7 13s7-8 7-13a7 7 0 0 0-7-7zm0 9.5A2.5 2.5 0 1 1 12 6.5a2.5 2.5 0 0 1 0 5z"/></svg>
  <h4>MAPPING</h4><p>Vestibulum vel metus sit amet turpis bibendum tincidunt vel sit amet quam habitant morbi tristique senectus..</p>
</div>
<div class="abs service" style="left:615px">
  <svg viewBox="0 0 24 24" fill="#fff"><path d="M2 5c0-1.5 1.5-3 3.5-3h8C15.5 2 17 3.5 17 5v5c0 1.5-1.5 3-3.5 3H8l-4 3v-3.3C2.8 12.3 2 11.3 2 10z"/><path d="M19 8h.5c1.4 0 2.5 1 2.5 2.5v4c0 1-.6 1.8-1.5 2.2V20l-3.5-3h-5c-1.2 0-2.2-.7-2.5-1.6H14c2.7 0 5-2 5-4.6z"/></svg>
  <h4>CONSULTING</h4><p>Vestibulum vel metus sit amet turpis bibendum tincidunt vel sit amet quam habitant morbi tristique senectus..</p>
</div>
<div class="abs service" style="left:885px">
  <svg viewBox="0 0 24 24" fill="none" stroke="#fff" stroke-width="1.8"><rect x="4" y="5" width="16" height="11" rx="1"/><path d="M1.5 18.5h21" stroke-linecap="round"/></svg>
  <h4>TRAINING</h4><p>Vestibulum vel metus sit amet turpis bibendum tincidunt vel sit amet quam habitant morbi tristique senectus..</p>
</div>

<section class="abs about">
  <svg class="abs" style="left:0;top:0" width="1200" height="435" viewBox="0 0 1200 435">
    <path d="M760 0 Q1000 70 1200 40 V0 H900 Q1060 40 1200 5" fill="var(--blue)"/>
    <path d="M360 435 Q500 380 760 410 L760 435Z" fill="var(--blue)"/>
  </svg>
  <div class="about-photo" role="img" aria-label="Photo of an engineer using a tablet to fly a drone over green hills" style="clip-path:ellipse(100% 100% at 0% 50%)"></div>
  <h2>ABOUT<br><span>PELHAM DRONE SOLUTIONS</span></h2>
  <p>Vestibulum vel metus sit amet turpis bibendum tincidunt vel sit amet quam. Pellentesque habitant morbi tristique senectus et netus et malesuada fames ac turpis egestas. Nunc consequat congue nulla eu imperdiet. Donec in est erat, id malesuada turpis. Nunc a dui id turpis convallis semper.</p>
  <span class="btn">READ MORE</span>
  <div class="badges">
    <div class="badge"><svg viewBox="0 0 24 24" fill="var(--blue)"><path d="M12 1l9 4v6c0 6-4 10-9 12C7 21 3 17 3 11V5z"/><path d="M7.5 12l3 3 6-6" stroke="#fff" stroke-width="2" fill="none"/></svg>SAFE.</div>
    <div class="badge"><svg viewBox="0 0 24 24" fill="var(--blue)"><path d="M5 1h10l4 4v18H5z"/><path d="M8 13l3 3 5-6" stroke="#fff" stroke-width="2" fill="none"/></svg>LEGAL.</div>
    <div class="badge"><svg viewBox="0 0 24 24" fill="var(--blue)"><circle cx="12" cy="12" r="11"/><path d="M7 12l3.5 3.5L17 9" stroke="#fff" stroke-width="2" fill="none"/></svg>INSURED.</div>
  </div>
</section>

<h2 class="title" style="top:1628px">OUR <em>PROJECTS</em></h2>
<div class="abs project" style="left:75px;top:1694px;width:510px;height:379px" role="img" aria-label="Video still of a drone over fields with a tablet showing a map">
  <div class="play"><svg width="26" height="26" viewBox="0 0 24 24" fill="#222"><path d="M7 4l13 8-13 8z"/></svg></div>
</div>
<div class="abs project" style="left:601px;top:1694px;width:256px;height:184px;background:linear-gradient(135deg,#c9cdd2,#8e96a0)" role="img" aria-label="Photo of an inspector watching a drone near a building"></div>
<div class="abs project" style="left:869px;top:1694px;width:256px;height:184px;background:linear-gradient(135deg,#d4d8de,#9aa56b)" role="img" aria-label="Photo of a drone producing a heat map over a field"></div>
<div class="abs project" style="left:601px;top:1892px;width:256px;height:181px;background:linear-gradient(135deg,#8e9bab,#7a6b55)" role="img" aria-label="Photo of a farmer watching a drone above a tractor"></div>
<div class="abs project" style="left:869px;top:1892px;width:256px;height:181px;background:linear-gradient(135deg,#aab6c2,#5d7555)" role="img" aria-label="Aerial photo of an industrial site by a river"></div>

<section class="abs solutions">
  <svg class="abs" style="left:0;top:0" width="1200" height="417" viewBox="0 0 1200 417">
    <path d="M750 0 Q1000 40 1200 60 V0 Q1050 20 900 0Z" fill="var(--blue)"/>
    <path d="M0 395 Q120 395 240 417 H0Z" fill="var(--blue)"/>
  </svg>
  <h2 class="title" style="top:42px">OUR <em>SOLUTIONS</em></h2>
  <p class="lead">Vestibulum vel metus sit amet turpis bibendum tincidunt vel sit amet quam. Pellentesque habitant morbi tristique senectus et netus et malesuada fames ac turpis egestas</p>
  <div class="sol" style="left:107px">
    <svg viewBox="0 0 24 24" fill="#333"><path d="M11 3a9 9 0 1 0 9.9 10H11z"/><path d="M13 1v10h10A10 10 0 0 0 13 1z"/></svg>
    <h4>CAPTURE</h4><p>Vestibulum vel metus sit amet turpis bibendum tincidunt vel sit amet quam pellentesque habitant morbi tristique..</p>
  </div>
  <div class="sol" style="left:435px">
    <svg viewBox="0 0 24 24" fill="#333"><path d="M9 2l1 2.2 2.3.5-.2 2.4 1.8 1.6-1.6 1.8.2 2.4-2.4.3L9 15l-1.2-2-2.4-.4.3-2.4L4 8.5l1.8-1.6-.1-2.4 2.3-.4zM9 6.3a2.3 2.3 0 1 0 0 4.6 2.3 2.3 0 0 0 0-4.6z"/><path d="M17 12l.8 1.5 1.6.3-.2 1.7 1.3 1.2-1.2 1.2.2 1.7-1.7.2-.8 1.5-1-1.4-1.7-.3.2-1.7-1.2-1.2 1.3-1.1-.1-1.7 1.6-.3zm0 3a1.5 1.5 0 1 0 0 3 1.5 1.5 0 0 0 0-3z"/></svg>
    <h4>PROCESS</h4><p>Vestibulum vel metus sit amet turpis bibendum tincidunt vel sit amet quam pellentesque habitant morbi tristique..</p>
  </div>
  <div class="sol" style="left:763px">
    <svg viewBox="0 0 24 24" fill="#333"><path d="M5 1h9l5 5v17H5z"/><path d="M8 11h8M8 14h8M8 17h8" stroke="#efefef" stroke-width="1.4"/></svg>
    <h4>DELIVER</h4><p>Vestibulum vel metus sit amet turpis bibendum tincidunt vel sit amet quam pellentesque habitant morbi tristique..</p>
  </div>
</section>

<h2 class="title" style="top:2585px">OUR <em>CLIENT SAYS..</em></h2>
<div class="abs avatar" role="img" aria-label="Client portrait photo"></div>
<p class="abs quote">" Vestibulum vel metus sit amet turpis bibendum tincidunt vel sit amet quam. Pellentesque habitant morbi tristique senectus et netus et malesuada fames ac turpis egestas. Vestibulum vel metus sit amet turpis bibendum tincidunt vel sit amet quam. Pellentesque habitant morbi tristique senectus et netus et malesuada fames ac turpis egestas.."</p>
<div class="abs person"><b>-NAME HEADING</b><i>Company Name</i></div>
<div class="abs clients" aria-label="Client logos">
  <div class="client"><i></i>Norvale</div>
  <div class="client"><i></i>Ridgecomm</div>
  <div class="client"><i></i>Tallow Utility</div>
  <div class="client"><i></i>Brisk Build</div>
  <div class="client"><i></i>Ostrem Insure</div>
</div>
<div class="abs dots" style="left:581px;top:3000px"><i class="on"></i><i style="background:#333"></i><i style="background:#333"></i></div>

<footer class="abs footer">
  <div class="col" style="left:75px;top:48px">
    <div class="flogo"><b>PELHAM</b><small>DRONE SOLUTIONS</small></div>
    <p style="font-size:13px;margin-top:22px">Copyright © 2017, Company Name<br>All Right Reserved</p>
    <div class="social" style="margin-top:36px"><span></span><span></span><span></span><span></span><span></span></div>
  </div>
  <div class="col" style="left:370px">
    <h5>SITE MAP</h5>
    <ul><li>Home</li><li>About Us</li><li>Services</li><li>Projects</li><li>Contact Us</li></ul>
  </div>
  <div class="col" style="left:575px;width:250px">
    <h5>OUR SERVICES</h5>
    <ul><li>Inspections</li><li>Mapping</li><li>Consulting</li><li>Training</li></ul>
  </div>
  <div class="col" style="left:885px;width:300px">
    <h5>CONTACT ADDRESS</h5>
    <p style="color:var(--blue);font-weight:700;font-size:13px">PELHAM DRONE SOLUTIONS</p>
    <p style="margin-bottom:10px">1420 Harlow Lane<br>Smyrna, TN 37167</p>
    <div class="contact-line"><svg width="14" height="14" viewBox="0 0 24 24" fill="#fff"><path d="M6.6 10.8a15 15 0 0 0 6.6 6.6l2.2-2.2c.3-.3.7-.4 1-.2 1.1.4 2.3.6 3.6.6.6 0 1 .4 1 1V20c0 .6-.4 1-1 1A17 17 0 0 1 3 4c0-.6.4-1 1-1h3.5c.6 0 1 .4 1 1 0 1.3.2 2.5.6 3.6.1.3 0 .7-.2 1z"/></svg>615-382-9041</div>
    <div class="contact-line"><svg width="14" height="14" viewBox="0 0 24 24" fill="#fff"><path d="M2 5h20v14H2z"/><path d="M2 5l10 8 10-8" stroke="#262626" stroke-width="2" fill="none"/></svg>info@pelhamdronesolutions-example.com</div>
    <div class="contact-line"><svg width="14" height="14" viewBox="0 0 24 24" fill="#fff"><path d="M12 2a7 7 0 0 0-7 7c0 5 7 13 7 13s7-8 7-13a7 7 0 0 0-7-7zm0 9.5A2.5 2.5 0 1 1 12 6.5a2.5 2.5 0 0 1 0 5z"/></svg>Map Location</div>
  </div>
</footer>

</body>
</html>
```